Bramblewood Joinery Website

My client Bramblewood Joinery is looking for a redesign for a Word Press Website. Their current site is at www.bramblewoodjoinery.example They are a custom cabinet company, but also create bathroom, living room, bar and entertainment and bedroom cabinets too. They would like a design that emulates the master craftsman work they do yet a contemporary style.

Their current site was designed using Flash elements.

Target Market(s)

Home owners and builders of high end homes

Industry/Entity Type

Entertainment

Font styles to use
Serif
Decorative

Requirements
Must have
• Must show their work and logo using a contemporary style.
Nice to have
• Sliders that showcase their projects.

```html
<!DOCTYPE html>
<html lang="en">
<head>
<meta charset="utf-8">
<title>Bramblewood Joinery</title>
<link rel="stylesheet" href="https://fonts.googleapis.com/css2?family=Questrial&family=Raleway:wght@300;400;500&family=Roboto+Condensed:wght@300;400&display=swap">
<style>
:root{
  --green:#2fb52f;
  --green-dark:#1f8f1f;
  --green-nav-top:#3cc23c;
  --green-nav-bottom:#1e9a1e;
  --charcoal:#3d3d3d;
  --ink:#222;
  --muted:#777;
  --line:#d6d6d6;
  --white:#fff;
}
*{box-sizing:border-box;margin:0;padding:0}
html,body{width:1040px;height:1200px;overflow:hidden;background:var(--white)}
body{position:relative;font-family:"Raleway",sans-serif;color:var(--ink)}
.abs{position:absolute}

.top-bar{left:0;top:0;width:1040px;height:41px;background:var(--charcoal)}
.social{display:flex;gap:4px}
.social span{width:26px;height:26px;border-radius:4px;display:block}
.s1{background:#5bb8e6}.s2{background:#3b5a9a}.s3{background:#c4302b}.s4{background:#cb2027}.s5{background:#8a6a52}

.brand-badge{left:97px;top:8px;width:92px;height:92px;border-radius:50%;background:var(--white);box-shadow:0 0 0 2px #1a1a1a inset;display:flex;align-items:center;justify-content:center;text-align:center}
.brand-name{font-family:"Questrial",sans-serif;color:var(--green-dark);font-size:12.5px;line-height:1.25}

.search{left:666px;top:62px;height:28px;display:flex;border:1px solid #bbb}
.search-input{width:146px;font-size:11px;color:var(--muted);padding:7px 6px;border-right:1px solid #ccc;white-space:nowrap}
.search-select{width:86px;font-size:12px;color:#444;padding:6px 4px;position:relative}
.search-select::after{content:"";position:absolute;right:8px;top:12px;border:4px solid transparent;border-top-color:#999}
.search-btn{width:38px;background:var(--green-dark);display:flex;align-items:center;justify-content:center}

.main-nav{left:0;top:107px;width:1040px;height:41px;background:linear-gradient(var(--green-nav-top),var(--green-nav-bottom));display:flex;justify-content:center;gap:22px;align-items:center}
.main-nav a{font-family:"Roboto Condensed",sans-serif;font-weight:300;color:var(--white);font-size:13.5px;text-decoration:none}

.hero{left:0;top:148px;width:1040px;height:426px;background:linear-gradient(100deg,#d8d4cc 0%,#7a3e22 22%,#5a2a15 50%,#9a8f80 62%,#6b331a 80%,#4a2212 100%)}
.hero-counter{left:0;top:200px;width:1040px;height:100px;background:linear-gradient(180deg,rgba(190,180,165,0),rgba(170,160,145,.55),rgba(120,100,80,.2))}
.hero-caption{left:0;top:503px;width:1040px;height:71px;background:rgba(30,20,15,.82)}
.hero-title{left:99px;top:518px;font-family:"Questrial",sans-serif;color:var(--white);font-size:33px;white-space:nowrap}
.dots{left:891px;top:536px;display:flex;gap:7px}
.dots span{width:8px;height:8px;border-radius:50%;background:var(--white)}
.dots .on{background:var(--green)}

.news-title{left:94px;top:609px;font-family:"Questrial",sans-serif;color:var(--green);font-size:16.5px;white-space:nowrap}
.news-note{left:341px;top:612px;font-size:9px;color:#333;white-space:nowrap}
.news-form{left:552px;top:603px;display:flex;height:30px}
.news-input{width:210px;border:1px solid #bbb;font-size:12.5px;color:#aaa;padding:6px 9px;font-weight:300;white-space:nowrap}
.news-btn{width:80px;background:var(--green);color:var(--white);font-size:12.5px;display:flex;align-items:center;justify-content:center;border:1px solid var(--green-dark)}
.like{left:866px;top:608px;display:flex;gap:6px;font-size:10px}
.like-btn{border:1px solid #ccd;border-radius:2px;padding:3px 5px;color:#3b5a9a;background:#f4f6fb}
.like-count{border:1px solid #bbb;padding:3px 4px;color:#333}
.rule{left:95px;top:663px;width:848px;height:4px;background:var(--green)}

.section-head{font-family:"Questrial",sans-serif;font-size:17.5px;color:var(--ink);white-space:nowrap}
.welcome-text{left:95px;top:731px;width:410px;font-size:12.2px;line-height:20px}
.welcome-text p{margin-bottom:15px}
.read-more{left:95px;top:850px;font-size:12.2px;color:var(--green)}

.arrow{width:22px;height:22px}
.thumb{width:151px;height:92px;border:1px solid #aaa;display:flex;align-items:center;justify-content:center}
.thumb-label{font-size:12.3px}
.play{width:24px;height:17px;background:#111;border-radius:3px;display:flex;align-items:center;justify-content:center}

.card{top:896px;width:263px;height:176px;background:linear-gradient(#f7f7f7,#ececec);border:1px solid var(--line);box-shadow:inset 0 0 18px rgba(0,0,0,.06)}
.card-img{position:absolute;left:14px;top:20px;width:85px;height:57px}
.card-title{position:absolute;font-family:"Questrial",sans-serif;font-size:14.5px;color:var(--ink);white-space:nowrap}
.card-text{position:absolute;font-size:11.3px;color:var(--muted);font-weight:300;line-height:16.5px}
.bullets{position:absolute;list-style:none;font-size:11.3px;color:#555;line-height:16.5px;white-space:nowrap}
.bullets li{padding-left:10px;position:relative}
.bullets li::before{content:"";position:absolute;left:0;top:4px;border:4px solid transparent;border-left:4px solid var(--green);border-right:0}
.cta{position:absolute;left:21px;top:133px;width:221px;height:30px;background:linear-gradient(#8ef08e,#5fdc5f);border:1px solid var(--green);display:flex;align-items:center;justify-content:space-between;padding:0 10px;font-size:12px;color:#123;white-space:nowrap}

.footer{left:0;top:1115px;width:1040px;height:85px;background:var(--charcoal)}
.footer-badge{left:102px;top:1130px;width:48px;height:48px;border-radius:50%;background:var(--white);display:flex;align-items:center;justify-content:center}
.footer-badge span{font-family:"Questrial",sans-serif;font-size:6.5px;color:var(--green-dark);text-align:center;line-height:1.2}
.footer-text{left:157px;top:1135px;color:var(--white);font-size:12.5px;line-height:22px;font-family:"Roboto Condensed",sans-serif;font-weight:300;white-space:nowrap}
</style>
</head>
<body>

<div class="abs top-bar"></div>
<div class="abs social" style="left:796px;top:8px" aria-label="Social links">
  <span class="s1"></span><span class="s2"></span><span class="s3"></span><span class="s4"></span><span class="s5"></span>
</div>

<div class="abs brand-badge"><div class="brand-name">Bramblewood<br>Joinery</div></div>

<div class="abs search">
  <div class="search-input">Enter Keyword to search</div>
  <div class="search-select">Select One</div>
  <div class="search-btn">
    <svg width="16" height="16" viewBox="0 0 16 16"><circle cx="6.5" cy="6.5" r="5" fill="none" stroke="#fff" stroke-width="2"/><line x1="10.2" y1="10.2" x2="14.5" y2="14.5" stroke="#fff" stroke-width="2.4" stroke-linecap="round"/></svg>
  </div>
</div>

<nav class="abs main-nav">
  <a>HOME</a><a>WHO WE ARE</a><a>GETTING STARTED</a><a>CONTACT US</a><a>CUSTOMER EXPERIENCE</a><a>PROFESSIONAL</a><a>PORTFOLIO</a><a>CABINET HARDWARE</a>
</nav>

<div class="abs hero" role="img" aria-label="Photo of a kitchen with dark cherry wood cabinets and a granite-topped island"></div>
<div class="abs hero-counter"></div>
<div class="abs hero-caption"></div>
<div class="abs hero-title">Bramblewood Joinery Style</div>
<div class="abs dots"><span></span><span class="on"></span><span></span></div>

<div class="abs news-title">NEWSLETTER SUBSCRIPTION</div>
<div class="abs news-note">[be update on latest offers, disconects etc.]</div>
<div class="abs news-form"><div class="news-input">Enter your Email address</div><div class="news-btn">SUBSCRIBE</div></div>
<div class="abs like"><div class="like-btn">&#9650; Like</div><div class="like-count">12</div></div>
<div class="abs rule"></div>

<div class="abs section-head" style="left:96px;top:698px">WELCOME TO OUR OFFICAL WEBSITE!</div>
<div class="abs welcome-text">
  <p>Lorem ipsum dolor sit amet, consectetur adipiscing elit, sed do eiusmod tempor incididunt ut labore et dolore magna aliqua. Ut enim ad minim veniam, quis nostrud exercitation ullamco laboris nisi ut</p>
  <p>Lorem ipsum dolor sit amet, consectetur adipiscing elit, sed do eiusmod tempor incididunt ut labore et dolore magna aliqua. Ut enim ad minim</p>
</div>
<div class="abs read-more">Read More</div>

<div class="abs section-head" style="left:537px;top:698px">WATCH VIDEO OF OUR PRODUCTS</div>
<svg class="abs arrow" style="left:538px;top:771px" viewBox="0 0 22 22"><circle cx="11" cy="11" r="11" fill="#2fb52f"/><path d="M13 6l-5 5 5 5" fill="none" stroke="#fff" stroke-width="2"/></svg>
<svg class="abs arrow" style="left:920px;top:771px" viewBox="0 0 22 22"><circle cx="11" cy="11" r="11" fill="#2fb52f"/><path d="M9 6l5 5-5 5" fill="none" stroke="#fff" stroke-width="2"/></svg>
<div class="abs thumb" style="left:577px;top:735px;background:linear-gradient(135deg,#e8e6e0,#b8b2a6 50%,#3a3a3a)" role="img" aria-label="Video still of a white kitchen"><div class="play"><svg width="8" height="9"><path d="M0 0l8 4.5L0 9z" fill="#fff"/></svg></div></div>
<div class="abs thumb" style="left:752px;top:735px;background:linear-gradient(90deg,#d8d6d0,#c9c6be 50%,#5a5a5a)" role="img" aria-label="Video still of a bathroom with a freestanding tub"><div class="play"><svg width="8" height="9"><path d="M0 0l8 4.5L0 9z" fill="#fff"/></svg></div></div>
<div class="abs thumb-label" style="left:577px;top:836px">Kitchen</div>
<div class="abs thumb-label" style="left:752px;top:836px">Bathroom</div>

<div class="abs card" style="left:96px">
  <div class="card-img" style="background:linear-gradient(135deg,#5a4030,#d8d2c6)" role="img" aria-label="Photo of an entertainment wall unit"></div>
  <div class="card-title" style="left:110px;top:18px">ONE STPO SHOPING</div>
  <div class="card-text" style="left:111px;top:41px;width:140px">All the products in one loc tion for your new home or renovation.</div>
  <ul class="bullets" style="left:111px;top:95px"><li>Kitchen Cabinet</li><li>Bathroom</li><li>Bedroom</li><li>Baar and Entertainment</li></ul>
</div>

<div class="abs card" style="left:388px">
  <div class="card-img" style="background:linear-gradient(135deg,#2a2420,#7a6a5a)" role="img" aria-label="Photo of a dark kitchen island"></div>
  <div class="card-title" style="left:108px;top:18px">CUSTOM CABINATERY</div>
  <div class="card-text" style="left:110px;top:41px;width:145px">Look at the difference that a quality makes.</div>
  <ul class="bullets" style="left:113px;top:79px"><li>Kitchen Cabinetry</li></ul>
  <ul class="bullets" style="left:13px;top:104px;display:flex;gap:14px"><li>Bathroom Cabinetry</li><li>Other Areas</li></ul>
  <div class="cta"><span>SCHEDULE AN APPOINTMENT</span><svg width="20" height="20" viewBox="0 0 20 20"><circle cx="10" cy="10" r="10" fill="#1f8f1f"/><path d="M8 6l5 4-5 4z" fill="#fff"/></svg></div>
</div>

<div class="abs card" style="left:679px">
  <div class="card-img" style="background:linear-gradient(135deg,#e6e2da,#6a5a48 60%,#b04020)" role="img" aria-label="Photo of a kitchen interior"></div>
  <div class="card-title" style="left:108px;top:18px;font-size:13.5px">WHY BRAMBLEWOOD?</div>
  <div class="card-text" style="left:110px;top:41px;width:145px">Lorem ipsum dolor sit amet, consectetur adipiscing</div>
  <ul class="bullets" style="left:113px;top:82px;line-height:19px"><li>Reason 1 ipsum</li><li>Reason 2 ipsum</li><li>Reason 3 ipsum</li><li>Reason 4 lorem</li></ul>
</div>

<div class="abs footer"></div>
<div class="abs footer-badge"><span>Bramblewood<br>Joinery</span></div>
<div class="abs footer-text">418 Alder Mill Ln, Fernbrook, MI 48000, USA<br>© 2015 Bramblewood Joinery</div>
<div class="abs social" style="left:796px;top:1141px" aria-label="Social links">
  <span class="s1"></span><span class="s2"></span><span class="s3"></span><span class="s4"></span><span class="s5"></span>
</div>

</body>
</html>
```